Exciting opportunity to create logo and a label for our natural health brand.

About us

We are a customer centric health supplement brand who believes in natural medicine and high quality ingredients. We take a holistic approach to healthcare, with an eastern philosophy. We believe in being partners with our customers in their health care journey and are invested in their well being.

Our brand philosophy and values are attached (see Vorna philosophy.png). Our personality traits are:

- Natural
- Fresh
- Modern
- Balanced (in a holistic sense)

Task breakdown

1. Design a fresh feeling logo for us
- We want it to represent our values and high quality ingredients. We would like the quality of the product to be reflected in the branding and have a high end feel.
- Logo text must include Vorna Health Sciences
- We want the Vorna to be the focus of the logo (see uploaded image Vorna logo example.png)
The logo does not have to follow this layout, but we just want the Vorna to stand out. Feel free to use your creative license on this!

2. Create an attractive label to go on the supplement bottle
- The designs need to be eye catching, give a sense of high end ingredients and natural products and tie in with the logo to give a joined up feel.
- We are selling our products online and need them to really stand out from the competition.
- See examples of labels and packaging we like (1 -7 label design).

The initial label we would like you to design would be for our product Calm Drift. It is a product that assists in the management of Anxiety and stress. The label will appear on the bottle that holds the capsules for this supplement, see uploaded files (Example plain bottles.png). The bottles may be white as the picture shows or dark blue recyclable plastic or dark brown glass . We don't have the exact dimensions of the bottle yet, but I will follow up with these.

The label needs to include the following things:
1. The logo
2. The name of the product
3. The product is to help with the relief of Anxiety and Stress
4. Number of capsules the bottle contains
5. The back of the label should have
i) The ingredients
ii) Dosage
iii) Directions of use

Please use placeholder text where needed.

We look forward to seeing your design. Thank you.

```html
<!DOCTYPE html>
<html lang="en">
<head>
<meta charset="utf-8">
<title>Vorna Health Sciences – Calm Drift label</title>
<link rel="stylesheet" href="https://fonts.googleapis.com/css2?family=Barlow:wght@400;500;600&display=swap">
<style>
  :root {
    --page-bg: #f3f3f3;
    --label-pink: #d27880;
    --label-pink-deep: #c96f78;
    --label-pink-light: #dc838c;
    --botanical-tone: #c4687198;
    --ink: #151213;
  }
  * { margin: 0; padding: 0; box-sizing: border-box; }
  html, body {
    width: 1200px;
    height: 750px;
    overflow: hidden;
    background: var(--page-bg);
  }
  .canvas {
    position: relative;
    width: 1200px;
    height: 750px;
  }
  .label {
    position: absolute;
    left: 351px;
    top: 65px;
    width: 497px;
    height: 620px;
    overflow: hidden;
    background: linear-gradient(90deg, var(--label-pink-deep) 0%, var(--label-pink) 55%, var(--label-pink-light) 100%);
    font-family: "Barlow", sans-serif;
    color: var(--ink);
  }
  .botanical-art {
    position: absolute;
    left: 200px;
    top: 70px;
    width: 297px;
    height: 550px;
    background: radial-gradient(ellipse at 60% 55%, var(--botanical-tone) 0%, rgba(196,104,113,0.35) 45%, rgba(196,104,113,0) 75%);
  }
  .brand {
    position: absolute;
    left: 92px;
    top: 78px;
    width: 318px;
    text-align: center;
  }
  .brand-name {
    display: block;
    font-size: 124px;
    font-weight: 500;
    line-height: 1;
    letter-spacing: -0.01em;
  }
  .brand-descriptor {
    display: block;
    margin-top: 14px;
    font-size: 14px;
    font-weight: 500;
    letter-spacing: 0.78em;
    padding-left: 0.78em;
  }
  .product {
    position: absolute;
    left: 72px;
    top: 318px;
  }
  .product-name {
    font-size: 34px;
    font-weight: 600;
    line-height: 1.1;
  }
  .product-benefit {
    margin-top: 12px;
    font-size: 14px;
    font-weight: 500;
    line-height: 1.35;
    letter-spacing: 0.06em;
  }
  .capsule-count {
    position: absolute;
    left: 72px;
    top: 482px;
    font-size: 15px;
    font-weight: 500;
    letter-spacing: 0.06em;
  }
  .capsule-count strong {
    font-size: 19px;
    font-weight: 600;
    margin-right: 4px;
  }
</style>
</head>
<body>
<main class="canvas">
  <section class="label">
    <div class="botanical-art" role="img" aria-label="Faint line drawing of flowering herb stems and leaves"></div>
    <header class="brand">
      <span class="brand-name">Vorna</span>
      <span class="brand-descriptor">HEALTH SCIENCE</span>
    </header>
    <div class="product">
      <h1 class="product-name">Calm Drift</h1>
      <p class="product-benefit">Reduce stress and<br>anxiety naturally</p>
    </div>
    <p class="capsule-count"><strong>60</strong> capsules</p>
  </section>
</main>
</body>
</html>
```